Modern looking signage for dental office.

Exterior signage for passing cars
Updates
Need extra days to review
Target Market(s)
Cars passing by
Font styles to use
Sans Serif
Colors
3276b5
Requirements
Must have
- Logo
- OPEN ON SUTURDAY AND SUNDAY
- NIGHT CLINIC AVAILABLE
- PLEASE USE THE FONT TYPE IN FILE 4 UPLOADED BELOW.
- (847) 302-7469
- Modern looking

```html
<!DOCTYPE html>
<html lang="en">
<head>
<meta charset="utf-8">
<title>Crestpoint Dental – Exterior Sign</title>
<link href="https://fonts.googleapis.com/css2?family=Anton&family=Josefin+Sans:wght@300&family=Encode+Sans+Condensed:wght@400&display=swap" rel="stylesheet">
<style>
  :root {
    --page-bg: #e8ebee;
    --sign-white: #ffffff;
    --brand-blue: #1d5b9f;
    --ink-dark: #2b2b2b;
    --ink-black: #111111;
    --rule-grey: #8a8a8a;
  }
  html, body {
    margin: 0;
    padding: 0;
    width: 1200px;
    height: 1200px;
    overflow: hidden;
    background: var(--page-bg);
  }
  .sign {
    position: absolute;
    left: 50px;
    top: 250px;
    width: 1100px;
    height: 700px;
    background: var(--sign-white);
    box-shadow: 0 2px 10px rgba(0,0,0,0.12);
    overflow: hidden;
  }
  .sign-shapes {
    position: absolute;
    inset: 0;
  }
  .brand {
    position: absolute;
    left: 110px;
    top: 80px;
    display: flex;
    align-items: center;
    gap: 24px;
  }
  .brand-dot {
    flex: none;
    width: 112px;
    height: 112px;
    border: 2px solid var(--ink-dark);
    border-radius: 50%;
    box-sizing: border-box;
  }
  .brand-text {
    display: flex;
    flex-direction: column;
    align-items: flex-start;
  }
  .brand-name {
    font-family: "Josefin Sans", sans-serif;
    font-weight: 300;
    font-size: 62px;
    line-height: 1;
    color: var(--ink-dark);
    letter-spacing: 1px;
    white-space: nowrap;
    padding-top: 10px;
  }
  .tagline {
    margin-top: 14px;
    margin-left: 48px;
    font-family: "Encode Sans Condensed", sans-serif;
    font-weight: 400;
    font-size: 30px;
    line-height: 1;
    color: var(--ink-dark);
    letter-spacing: 0.5px;
    white-space: nowrap;
  }
  .headline {
    position: absolute;
    right: 40px;
    top: 308px;
    margin: 0;
    text-align: right;
    font-family: "Anton", sans-serif;
    font-weight: 400;
    font-size: 88px;
    line-height: 108px;
    color: var(--sign-white);
    letter-spacing: 2px;
    white-space: nowrap;
  }
  .hours {
    position: absolute;
    right: 40px;
    top: 566px;
    margin: 0;
    text-align: right;
    font-family: "Anton", sans-serif;
    font-weight: 400;
    font-size: 50px;
    line-height: 60px;
    color: var(--sign-white);
    letter-spacing: 1.5px;
    white-space: nowrap;
  }
  .phone {
    position: absolute;
    left: 40px;
    top: 578px;
    font-family: "Anton", sans-serif;
    font-weight: 400;
    font-size: 64px;
    line-height: 1;
    color: var(--ink-black);
    letter-spacing: 1px;
    white-space: nowrap;
  }
</style>
</head>
<body>
  <div class="sign">
    <svg class="sign-shapes" width="1100" height="700" viewBox="0 0 1100 700" aria-hidden="true">
      <line class="divider-rule" x1="0" y1="552" x2="480" y2="552" stroke="#8a8a8a" stroke-width="2"/>
      <polygon class="band-upper" points="360,300 1100,300 1100,530 460,530" fill="#1d5b9f"/>
      <polygon class="band-lower" points="470,552 1100,552 1100,700 540,700" fill="#1d5b9f"/>
    </svg>

    <div class="brand">
      <span class="brand-dot"></span>
      <div class="brand-text">
        <span class="brand-name">CRESTPOINT DENTAL</span>
        <span class="tagline">MODERN GENERAL DENTISTRY</span>
      </div>
    </div>

    <h1 class="headline">Night Clinic<br>Available</h1>
    <p class="hours">Open on<br>Saturday and Sunday</p>

    <div class="phone">(847) 302-7469</div>
  </div>
</body>
</html>
```